Wandering Rooms Stationary Set

Wandering Rooms is a bespoke interior design firm set to provide services to VIP clients with elegance and minimalism is the main theme for our stationary set. We require a full stationary set covering A4 letterhead, A4 & A3 envelopes, business cards, USB's, CDs, email signature and any other item the designer sees fit. logo is already designed and finalized, and we require the designer to use it as is without modifying the logo.

Address to be used on letterhead / business cards ...etc shall be as follows:

Phone : +971 2 518 2047
P.O. Box : 309186
Address: Block C&D, Bldg. 47, Court 12, Abu Dhabi, United Arab Emirates
Website: www.wanderingrooms-example.com

Target Market(s)

VIP Clients

Industry/Entity Type

Interior Design

Font styles to use
Other font styles liked:
• something to be unique

Colors

Designer to choose colors to be used in the design.

Requirements
Must have
• Elegant, minimalistic
Nice to have
• Simple yet elegant design having a sharp yet clean cut format
Should not have
• No additional colours, just colours that are used in the logo (silver, black or gold)

```html
<!DOCTYPE html>
<html lang="en">
<head>
<meta charset="utf-8">
<title>Wandering Rooms — Business Card</title>
<link rel="stylesheet" href="https://fonts.googleapis.com/css2?family=Allura&family=Cormorant+Garamond:wght@400;500&display=swap">
<style>
  :root {
    --backdrop: #1c1c1d;
    --card: #2a2a2a;
    --card-edge: #333333;
    --gold: #c6a350;
    --gold-deep: #a8843a;
    --silver: #9c9c9c;
    --silver-light: #cfcfcf;
    --text-grey: #8e8e8e;
    --ink: #1d1d1d;
  }
  html, body {
    margin: 0;
    padding: 0;
    width: 1200px;
    height: 800px;
    overflow: hidden;
    background: var(--backdrop);
  }
  .canvas {
    position: relative;
    width: 1200px;
    height: 800px;
    font-family: "Cormorant Garamond", Georgia, serif;
  }
  .card {
    position: absolute;
    left: 320px;
    width: 560px;
    height: 320px;
    background: var(--card);
    box-shadow: 0 12px 30px rgba(0,0,0,0.45);
    border: 1px solid var(--card-edge);
    box-sizing: border-box;
    overflow: hidden;
  }
  .card--front { top: 50px; }
  .card--back { top: 430px; }

  /* Front */
  .front-mark {
    position: absolute;
    inset: 0;
    display: flex;
    align-items: center;
    justify-content: center;
  }
  .front-mark__name {
    font-size: 46px;
    font-weight: 400;
    letter-spacing: 0.04em;
    color: var(--silver);
  }

  /* Back */
  .brand-name {
    position: absolute;
    left: 40px;
    top: 96px;
    font-size: 34px;
    font-weight: 400;
    letter-spacing: 0.04em;
    color: var(--gold);
  }
  .person {
    position: absolute;
    right: 40px;
    top: 34px;
    text-align: right;
  }
  .person__name {
    font-family: "Allura", cursive;
    font-size: 32px;
    color: var(--gold);
    line-height: 1;
  }
  .person__title {
    font-size: 15px;
    color: var(--silver-light);
    margin-top: 2px;
  }
  .contact {
    position: absolute;
    right: 40px;
    top: 196px;
    text-align: right;
    font-size: 12.5px;
    color: var(--text-grey);
    line-height: 1.6;
  }
  .contact__label {
    color: var(--gold);
    font-weight: 500;
    margin-right: 4px;
  }
  .address {
    position: absolute;
    left: 40px;
    bottom: 44px;
    font-size: 12.5px;
    color: var(--text-grey);
    line-height: 1.45;
  }
  .web-band {
    position: absolute;
    left: 0;
    right: 0;
    bottom: 0;
    height: 30px;
    background: linear-gradient(90deg, rgba(198,163,80,0) 22%, var(--gold-deep) 48%, var(--gold) 100%);
    display: flex;
    align-items: center;
    justify-content: flex-end;
    padding-right: 40px;
  }
  .web-band__url {
    font-size: 13px;
    letter-spacing: 0.14em;
    color: var(--ink);
    font-weight: 500;
  }
  .contact-glow {
    position: absolute;
    right: 0;
    top: 190px;
    width: 300px;
    height: 54px;
    background: linear-gradient(90deg, rgba(255,255,255,0) 0%, rgba(255,255,255,0.03) 100%);
  }
</style>
</head>
<body>
  <main class="canvas">
    <section class="card card--front" aria-label="Business card front">
      <div class="front-mark">
        <span class="front-mark__name">Wandering Rooms</span>
      </div>
    </section>

    <section class="card card--back" aria-label="Business card back">
      <div class="brand-name">Wandering Rooms</div>

      <div class="person">
        <div class="person__name">Daniel Hart</div>
        <div class="person__title">President</div>
      </div>

      <div class="contact-glow"></div>
      <div class="contact">
        <div><span class="contact__label">P :</span>+971 2 518 2047</div>
        <div><span class="contact__label">E :</span>info@wanderingrooms-example.com</div>
      </div>

      <div class="address">
        P.O. Box : 309186<br>
        Block C&amp;D, Bldg. 47, Court 12<br>
        Abu Dhabi, United Arab Emirates
      </div>

      <div class="web-band">
        <span class="web-band__url">www.wanderingrooms-example.com</span>
      </div>
    </section>
  </main>
</body>
</html>
```